Design 4 pages for an event discovery website

This is a contest for the design of 4 pages for an events discovery website. The feature is part of the new sign-up process.

Please see the attached document for a full scope, mockups and the parent category icons.

Target Market(s)

18-35 Australian event goers

Industry/Entity Type

Events

Number of Pages Required

4 page

```html
<!DOCTYPE html>
<html lang="en">
<head>
<meta charset="utf-8">
<title>Eventora – Signup</title>
<link href="https://fonts.googleapis.com/css2?family=Roboto:wght@300;400&display=swap" rel="stylesheet">
<style>
:root{
  --brand-blue:#0a6fc2;
  --page-grey:#f3f3f3;
  --white:#ffffff;
  --text-dark:#2b2b2b;
  --text-muted:#8a8a8a;
  --border:#d6d6d6;
  --error:#ee1c25;
  --cta-orange:#f15a24;
}
*{margin:0;padding:0;box-sizing:border-box}
html,body{width:1200px;height:821px;overflow:hidden;background:var(--white)}
body{font-family:'Roboto',Arial,sans-serif;font-weight:300;color:var(--text-dark);position:relative}
ul{list-style:none}

.site-header{position:absolute;left:0;top:0;width:1200px;height:103px;background:var(--white)}
.brand-name{position:absolute;left:103px;top:28px;font-size:34px;font-weight:400;color:var(--brand-blue);line-height:42px}
.nav-link{position:absolute;left:496px;top:42px;font-size:17px;font-weight:400;color:var(--text-dark)}
.search-box{position:absolute;left:614px;top:29px;width:244px;height:46px;border:1px solid var(--border);display:flex;align-items:center;padding-left:14px;gap:9px;font-size:14px;color:var(--text-muted);font-weight:400}
.btn-outline,.btn-solid{position:absolute;top:29px;width:105px;height:46px;display:flex;align-items:center;justify-content:center;font-size:17px;font-weight:400}
.btn-outline{left:878px;border:2px solid #b8b8b8;color:var(--text-dark);background:var(--white)}
.btn-solid{left:991px;background:var(--brand-blue);color:var(--white)}

.signup-area{position:absolute;left:0;top:103px;width:1200px;height:652px;background:var(--page-grey)}
.form-title{position:absolute;left:124px;width:347px;top:49px;text-align:center;font-size:27px;font-weight:300}
.field{position:absolute;left:124px;width:347px;height:57px;background:var(--white);border:1px solid var(--border);display:flex;align-items:center;justify-content:space-between;padding:0 18px;font-size:14.5px;font-weight:400;color:var(--text-muted)}
.field-error{position:absolute;left:486px;font-size:14px;font-weight:400;color:var(--error);line-height:20px}
.signup-button{position:absolute;left:125px;top:569px;width:346px;height:64px;background:var(--cta-orange);color:var(--white);font-size:25px;font-weight:400;display:flex;align-items:center;justify-content:center}

.benefit{position:absolute;left:614px;width:500px;display:flex;gap:19px;font-size:17.5px;font-weight:300;line-height:25px;color:var(--text-dark)}
.benefit-marker{flex:none;width:20px;height:20px;margin-top:2px}

.site-footer{position:absolute;left:0;top:755px;width:1200px;height:66px;background:var(--white)}
.copyright{position:absolute;left:0;width:1200px;top:27px;text-align:center;font-size:14px;font-weight:400;color:var(--text-dark)}
</style>
</head>
<body>
<header class="site-header">
  <div class="brand-name">Eventora</div>
  <div class="nav-link">Find Events</div>
  <div class="search-box">
    <svg width="16" height="16" viewBox="0 0 16 16"><circle cx="6.5" cy="6.5" r="5" fill="none" stroke="#b0b0b0" stroke-width="2"/><line x1="10.3" y1="10.3" x2="14.5" y2="14.5" stroke="#b0b0b0" stroke-width="2.2"/></svg>
    <span>Search</span>
  </div>
  <div class="btn-outline">Sign Up</div>
  <div class="btn-solid">Login</div>
</header>

<main class="signup-area">
  <h1 class="form-title">Signup</h1>
  <div class="field" style="top:107px">Username</div>
  <div class="field-error" style="top:119px">Invalid Username</div>
  <div class="field" style="top:173px">E Mail Address</div>
  <div class="field-error" style="top:176px">Invalid Email<br>Address</div>
  <div class="field" style="top:240px">Password</div>
  <div class="field" style="top:304px">Confirm Password</div>
  <div class="field" style="top:369px">First Name</div>
  <div class="field" style="top:434px">Last Name</div>
  <div class="field" style="top:500px">Date of Birth
    <svg width="18" height="18" viewBox="0 0 18 18"><rect x="1" y="3" width="16" height="14" fill="none" stroke="#9a9a9a" stroke-width="1.5"/><line x1="1" y1="7" x2="17" y2="7" stroke="#9a9a9a" stroke-width="1.5"/><line x1="5" y1="1" x2="5" y2="5" stroke="#9a9a9a" stroke-width="1.5"/><line x1="13" y1="1" x2="13" y2="5" stroke="#9a9a9a" stroke-width="1.5"/><path d="M4 10h10M4 13.5h10M7.3 7v10M10.6 7v10" stroke="#9a9a9a" stroke-width="1"/></svg>
  </div>
  <div class="signup-button">Signup</div>

  <ul>
    <li class="benefit" style="top:55px"><svg class="benefit-marker" viewBox="0 0 20 20"><rect width="20" height="20" fill="#0a6fc2"/><path d="M8.5 6.5l3.5 3.5-3.5 3.5" fill="none" stroke="#fff" stroke-width="1.8"/></svg><span>Get personalised event recommendations</span></li>
    <li class="benefit" style="top:118px"><svg class="benefit-marker" viewBox="0 0 20 20"><rect width="20" height="20" fill="#0a6fc2"/><path d="M8.5 6.5l3.5 3.5-3.5 3.5" fill="none" stroke="#fff" stroke-width="1.8"/></svg><span>Get notified about your favourite events -<br>never miss out again</span></li>
    <li class="benefit" style="top:198px"><svg class="benefit-marker" viewBox="0 0 20 20"><rect width="20" height="20" fill="#0a6fc2"/><path d="M8.5 6.5l3.5 3.5-3.5 3.5" fill="none" stroke="#fff" stroke-width="1.8"/></svg><span>Follow all your favourite artists, musicians, teams and players in one place</span></li>
    <li class="benefit" style="top:281px"><svg class="benefit-marker" viewBox="0 0 20 20"><rect width="20" height="20" fill="#0a6fc2"/><path d="M8.5 6.5l3.5 3.5-3.5 3.5" fill="none" stroke="#fff" stroke-width="1.8"/></svg><span>Follow your favourite local venues to know everything happening there</span></li>
    <li class="benefit" style="top:368px"><svg class="benefit-marker" viewBox="0 0 20 20"><rect width="20" height="20" fill="#0a6fc2"/><path d="M8.5 6.5l3.5 3.5-3.5 3.5" fill="none" stroke="#fff" stroke-width="1.8"/></svg><span>Get curated news and feature content on your favourite artists (coming soon)</span></li>
    <li class="benefit" style="top:457px"><svg class="benefit-marker" viewBox="0 0 20 20"><rect width="20" height="20" fill="#0a6fc2"/><path d="M8.5 6.5l3.5 3.5-3.5 3.5" fill="none" stroke="#fff" stroke-width="1.8"/></svg><span>Invite your mates to events via Palvine (PV sign-up only)</span></li>
  </ul>
</main>

<footer class="site-footer">
  <div class="copyright">Copyrights @ 2015 All Rightys Reserved</div>
</footer>
</body>
</html>
```